Systems and Technology Consultants - Website

Design & Build a website for a new company which operates in the Systems and Technology space for Transportation, Government and Commercial sectors.

Overall design should be minimalist in nature.
Should also have a feed that provides news and event updates on the main page.
Logo has already been awarded and should be incorporated into the site.

We like the overall layout, functionality and simplicity of the below sites. Submitted designs could be similar to or a combination of the aspects on these sites, or perhaps a whole different concept - we are open to new ideas.
Norvique.com
Teblo.it

Update 1 Dated 27 May 2014

All I am moving away from the Teblo.it website and would like it to be more aligned with Norvique.com not only in layout but in functionality. I will be extending the deadline of this design brief for two weeks to incorporate additional requirements and will add addtional funding to the project.

Apologies for not having more information available to provide but with so many submissions its getting confusing.

Thanks Derek

Please note that the brief has been updated and the deadline has been extended.

Important: We will need two language versions of the website, English and Arabic; the website is hosted on HostPelican

Hello All, Thank you for your submissions. We have narrowed it down to the final 6 designers and I just wanted to take a moment and provide a bit of feedback regarding the concepts that we like and the modifications we are looking for. First, let me mention some of the design functions we like. - At the top of the homepage we really like the "region" or "language" tab so that the website can be viewed in both English and Arabic. - We like the homepage to have clear color variation so that the different sections of the homepage are distinct. Additionally, we like the bottom portion of the homepage to be in red. We feel that draws attention to our contact information. Again, we would like the colors to integrate black, gray-scale, red, etc. - Having a search tab at the top of the home page, or integrated into the main image, so that the site is easy to navigate. - We especially like the main image to have the scrolling tabs at the bottom so it is easy to browse the services offered (Consultancy, Solutions Architecture, Masters Systems Integration, Independent Design Review). - In regards to the services offered tab we really like the idea that a few people presented that have the outside of our logo with an icon in the middle of consultancy, solutions, etc., etc. Secondly, as mentioned in our brief we really enjoy the design of norvique site. Specially, we enjoy the strong iconic images they use, the way the tabs at the top scroll easily, and contact us page that generates an email. Lastly, I've included some photos of the concept we have been working on. What we are trying to demonstrate is how our company offers a range of services that are essentially linked together. We provide individual services that when combined present the full service package. We would like this concept to be integrated into the over concept of our website. Please feel free to ask for clarification of any of the above points or contact us if you have any additional questions. We appreciate all of your hard work and are very excited to see the updated designs. Best, Marta Vennick Quelbrant Senior Program Manager marta.vennick@quelbrant-example.com

Industry/Entity Type

Government

Font styles to use
Serif
Sans Serif

Requirements
Must have
• Must work on/adapt to various/mobile devices (responsive)
Must be simple and straightforward
Colors should be in line/matching with logo
2 language versions: English and Arabic (no Thai)
Services should be the first group/row of items after/below the main image
Note: the website will be hosted by hostpelican
Nice to have
• Submit feedback form
What's New section
The banner at the bottom of the site should not be too large; we would like a narrow one more
It would be nice if the header/top banner (with Home, About, etc. tabs) could stay in place as you scroll down (like Norvique and Chatterloop)
We will likely only use one image with a Company slogan on the Home page rather than a carousel of images to rotate through
Should not have
• This is the existing website: http://www.quelbrant-example.org
We do not like the animation, the way the banner icons/titles bounce
Not simple enough, we don't like the functionality or how pages load so slowly
We do not like the logo centered - it should be at the left
The banner and its tabs should not be towards the right, we would like them to be centered, to go all the way across and to be below the logo

```html
<!DOCTYPE html>
<html lang="en">
<head>
<meta charset="utf-8">
<title>Quelbrant – Systems Professionals</title>
<link rel="stylesheet" href="https://fonts.googleapis.com/css2?family=Open+Sans:ital,wght@0,400;0,600;1,600&display=swap">
<style>
:root{
  --red:#e02026;
  --ink:#222;
  --text:#555;
  --muted:#999;
  --orange:#f4a068;
  --panel:#eeedee;
  --footer:#7a7879;
  --line:#dcdcdc;
}
*{margin:0;padding:0;box-sizing:border-box}
html,body{width:809px;height:1200px;overflow:hidden;background:#fff}
body{position:relative;font-family:"Open Sans",Arial,sans-serif;color:var(--ink)}
.abs{position:absolute}

/* header */
.brand{left:88px;top:30px;display:flex;align-items:center;gap:7px}
.brand-mark{width:16px;height:16px;background:var(--red)}
.brand-name{font-size:17px;font-weight:600;color:var(--red);letter-spacing:3px}
.search{left:622px;top:28px;width:100px;font-size:7px;color:var(--muted);display:flex;align-items:center;justify-content:space-between}
.search span{border-bottom:1px dashed #ccc;padding-left:30px}
.nav{left:357px;top:63px;display:flex;gap:22px;font-size:9.5px}
.nav a{color:var(--ink);text-decoration:none}
.nav a.active{color:var(--red)}

/* hero */
.hero{left:0;top:97px;width:809px;height:295px;background:linear-gradient(135deg,#9fb9e0 0%,#c9d8ef 40%,#8eaee0 70%,#6f93d4 100%)}
.hero-title{left:357px;top:218px;font-size:34px;font-style:italic;font-weight:600;color:var(--red);letter-spacing:-.5px}
.hero-arrow{top:222px;width:36px;height:46px;background:rgba(80,60,50,.55);color:#ddd;font-size:26px;display:flex;align-items:center;justify-content:center;font-weight:300}
.dots{left:384px;top:373px;display:flex;gap:3px;align-items:center}
.dots i{width:7px;height:7px;border-radius:50%;background:#8a8a8a;display:block}
.dots i.on{width:10px;height:10px;background:#333}

/* vision */
h2{font-size:17px;font-weight:400;color:var(--red)}
.vision{left:88px;top:434px;width:330px}
.vision p{font-size:7.4px;line-height:14px;color:var(--text);text-align:justify;margin-top:14px}
.vision h2{margin-bottom:6px}
.industries{left:456px;top:415px;width:265px;height:247px;border:1px solid var(--line);border-radius:4px}
.industries h2{position:absolute;left:22px;top:19px}
.industries .lead{position:absolute;left:21px;top:58px;font-size:7.3px;color:#444}
.ind{position:absolute;width:80px;text-align:center;font-size:7.3px;line-height:9px;color:#333}
.ind svg{display:block;margin:0 auto 5px;width:38px;height:40px}

/* services */
.services-title{left:88px;top:703px}
.pager{left:686px;top:704px;width:35px;height:21px;border:1px solid #ccc;background:#f3f3f3;font-size:12px;color:#444;text-align:center;line-height:19px;letter-spacing:2px}
.card{top:750px;width:204px}
.card .photo{height:101px}
.card h3{font-size:9.5px;font-weight:400;margin-top:6px}
.card p{font-size:7.4px;line-height:14px;color:var(--text);margin-top:2px;position:relative}
.card p b{position:absolute;right:2px;bottom:0;font-weight:400;color:var(--muted)}

/* contact */
.contact-panel{left:88px;top:938px;width:633px;height:222px;background:var(--panel)}
.contact{left:105px;top:953px;width:380px}
.contact h3{font-size:12.5px;font-weight:400;margin-bottom:12px}
.contact h4{font-size:9px;font-weight:400;margin-bottom:2px}
.contact p{font-size:7.2px;line-height:12.8px;color:#333;margin-bottom:12px}
.news-title{left:523px;top:953px;font-size:12.5px;display:flex;align-items:center;gap:6px}
.news-item{left:520px;width:201px;height:54px;display:flex;gap:8px;padding-left:4px}
.news-item.sep{border-bottom:1px solid #d3d3d3}
.news-item .thumb{width:43px;height:32px;flex:none;margin-top:2px}
.news-item .txt{font-size:7.3px;line-height:10.8px;color:#555}
.news-item .txt strong{font-weight:400;color:#222;font-size:7.8px}
.news-item .txt span{color:#222}

/* footer */
.footer{left:0;top:1160px;width:809px;height:40px;background:var(--footer)}
.social{left:96px;top:1173px;display:flex;gap:12px}
.social i{width:10px;height:10px;border-radius:50%;background:#fff;display:block}
.copy{right:95px;top:1174px;font-size:7.5px;color:#fff}
</style>
</head>
<body>

<header>
  <div class="abs brand"><i class="brand-mark"></i><span class="brand-name">QUELBRANT</span></div>
  <div class="abs search"><span>Enter keyword</span>
    <svg width="9" height="9" viewBox="0 0 9 9"><circle cx="3.5" cy="3.5" r="2.5" fill="none" stroke="#888" stroke-width="1.2"/><line x1="5.4" y1="5.4" x2="8.5" y2="8.5" stroke="#888" stroke-width="1.4"/></svg>
  </div>
  <nav class="abs nav">
    <a class="active" href="#">Home</a><a href="#">Business Unit</a><a href="#">Services</a><a href="#">About Us</a><a href="#">Locations</a><a href="#">Contact Us</a>
  </nav>
</header>

<section>
  <div class="abs hero" role="img" aria-label="Hands measuring an architectural blueprint in blue tones"></div>
  <div class="abs hero-arrow" style="left:0">&#x27E8;</div>
  <div class="abs hero-arrow" style="left:773px">&#x27E9;</div>
  <div class="abs hero-title">Systems Professionals</div>
  <div class="abs dots"><i class="on"></i><i></i><i></i><i></i></div>
</section>

<section class="abs vision">
  <h2>Our Vision</h2>
  <p>quelbrant specializes in delivering quality professional services and technical projects that support larger business goals. systems are tools that support a greater business function and need. we understand that most technical projects are conceptualized to support a larger vision with actual business goals in mind and ensure that all of our professional and certified expertise is included in our professional services to meet those goals.</p>
  <p>quelbrant recognizes the middle east and greater asia regions are economic growth markets with developing infrastructure projects requiring specialist systems and technical expertise. accordingly, quelbrant has evolved its presence in the regions to meet client demands and expectations.</p>
  <p>our ultimate goal is to provide quality, technical and professional services on projects of any scale and/or complexity, from conception through to completion. our philosophy is simple; stick to what you are good at and be the best at it.</p>
</section>

<section class="abs industries">
  <h2>Various Industies</h2>
  <div class="lead">quelbrant provide services throughout the following industries</div>
  <div class="ind" style="left:26px;top:78px">
    <svg viewBox="0 0 38 40"><rect width="38" height="40" fill="var(--orange)"/><path d="M19 14 L13 33 M19 14 L25 33 M15 26 H23" stroke="#fff" stroke-width="2" fill="none"/><circle cx="19" cy="12" r="2" fill="#fff"/><path d="M13 7 Q10 12 13 17 M25 7 Q28 12 25 17" stroke="#fff" stroke-width="1.5" fill="none"/></svg>
    Tele-<br>communications</div>
  <div class="ind" style="left:107px;top:78px">
    <svg viewBox="0 0 38 40"><rect width="38" height="40" fill="var(--orange)"/><path d="M29 9 L12 26 L8 25 L7 27 L12 29 L14 34 L16 33 L15 29 L32 12 Z M22 14 L10 12 L8 14 L18 18 Z M25 17 L27 29 L25 31 L21 21 Z" fill="#fff"/></svg>
    Airports</div>
  <div class="ind" style="left:184px;top:78px">
    <svg viewBox="0 0 38 40"><rect width="38" height="40" fill="var(--orange)"/><circle cx="19" cy="20" r="12" fill="none" stroke="#fff" stroke-width="2"/><path d="M19 13 Q24 20 22 23 A3.5 3.5 0 0 1 16 23 Q14 20 19 13 Z" fill="#fff"/></svg>
    Water Treatment<br>Plants</div>
  <div class="ind" style="left:26px;top:166px">
    <svg viewBox="0 0 38 40"><rect width="38" height="40" fill="var(--orange)"/><path d="M19 10 L12 34 M19 10 L26 34 M14 26 L24 30 M24 26 L14 30 M15 20 H23 M10 14 H28" stroke="#fff" stroke-width="2" fill="none"/></svg>
    Oil &amp; Gas</div>
  <div class="ind" style="left:107px;top:166px">
    <svg viewBox="0 0 38 40"><rect width="38" height="40" fill="var(--orange)"/><circle cx="19" cy="10" r="3" fill="none" stroke="#fff" stroke-width="2"/><path d="M19 13 V33 M13 17 H25 M9 24 Q11 33 19 33 Q27 33 29 24" stroke="#fff" stroke-width="2.2" fill="none"/></svg>
    Ports</div>
  <div class="ind" style="left:184px;top:166px">
    <svg viewBox="0 0 38 40"><rect width="38" height="40" fill="var(--orange)"/><rect x="11" y="9" width="16" height="21" rx="4" fill="#fff"/><rect x="14" y="13" width="10" height="6" fill="var(--orange)"/><circle cx="15" cy="25" r="1.5" fill="var(--orange)"/><circle cx="23" cy="25" r="1.5" fill="var(--orange)"/><path d="M13 30 L10 35 M25 30 L28 35" stroke="#fff" stroke-width="2"/></svg>
    Rails</div>
</section>

<section>
  <h2 class="abs services-title">Our Services</h2>
  <div class="abs pager">&lt;&gt;</div>
  <article class="abs card" style="left:88px">
    <div class="photo" role="img" aria-label="Blue circuit board close-up" style="background:linear-gradient(135deg,#0f4fa8,#2f8be0 55%,#0b3a82)"></div>
    <h3>Engineering</h3>
    <p>Lorem ipsum dolor sit amet, consectetur adipisicing elit, sed do eiusmod tempor incididunt ut.. <b>More</b></p>
  </article>
  <article class="abs card" style="left:302px">
    <div class="photo" role="img" aria-label="Rolled blueprints in blue light" style="background:linear-gradient(135deg,#1d3e6e,#6c93c7 50%,#2d5a94)"></div>
    <h3>Construction</h3>
    <p>Lorem ipsum dolor sit amet, consectetur adipisicing elit, sed do eiusmod tempor incididunt ut.. <b>More</b></p>
  </article>
  <article class="abs card" style="left:516px">
    <div class="photo" role="img" aria-label="Operations control room with monitoring desks" style="background:linear-gradient(180deg,#8a6a5a,#c7a98e 45%,#6b4a3c)"></div>
    <h3>Operations</h3>
    <p>Lorem ipsum dolor sit amet, consectetur adipisicing elit, sed do eiusmod tempor incididunt ut.. <b>More</b></p>
  </article>
</section>

<section>
  <div class="abs contact-panel"></div>
  <div class="abs contact">
    <h3>Contact Us</h3>
    <h4>Bangkok address :</h4>
    <p>41 lamphon garden rd, khlong nuea, bangkok 10240<br>phone numbers: +(66)-02-555-0148-2<br>email: info@quelbrant-example.org</p>
    <h4>Sukumvit address:</h4>
    <p>210/7 meridian court, orchid lane 14, bang rak, bangkok 10500<br>phone numbers: +(66)-02-555-0193</p>
    <h4>Pattaya address :</h4>
    <p>&nbsp;17/3 m.4 seaview road 12, na kluea, chonburi 20155<br>phone numbers: +(66)-038-555-017</p>
  </div>
  <div class="abs news-title">
    <svg width="13" height="12" viewBox="0 0 13 12"><rect x=".5" y=".5" width="12" height="11" fill="none" stroke="#444"/><path d="M2.5 3 H10.5 M2.5 5.5 H10.5 M2.5 8 H7" stroke="#444"/></svg>
    News &amp; Events</div>
  <div class="abs news-item sep" style="top:984px">
    <div class="thumb" role="img" aria-label="Industrial plant at dusk" style="background:linear-gradient(180deg,#3a5f9a,#c9b66a 60%,#2d3c2a)"></div>
    <div class="txt"><strong>Temporibus autem quibusdam</strong><br>13 May 2014<br>11.30 am- 2.30 pm<br><span>More...</span></div>
  </div>
  <div class="abs news-item sep" style="top:1038px">
    <div class="thumb" role="img" aria-label="Blue server racks" style="background:linear-gradient(135deg,#0d2f8a,#2f6fd6)"></div>
    <div class="txt"><strong>Temporibus autem quibusdam</strong><br>23 April 2014<br>11.30 am- 2.30 pm<br><span>More...</span></div>
  </div>
  <div class="abs news-item" style="top:1093px">
    <div class="thumb" role="img" aria-label="Technology meeting scene" style="background:linear-gradient(135deg,#55606e,#aab4c2 55%,#3b4350)"></div>
    <div class="txt"><strong>Temporibus autem quibusdam</strong><br>23 March 2014<br>11.30 am- 2.30 pm<br><span>More...</span></div>
  </div>
</section>

<footer>
  <div class="abs footer"></div>
  <div class="abs social"><i></i><i></i><i></i><i></i><i></i></div>
  <div class="abs copy">© 2014 All rights reserved</div>
</footer>

</body>
</html>
```